Redesign of business card for Cedar Ridge Mechanical

We are looking for a new design for our business cards for Cedar Ridge Mechanical. We are a plumbing & HVAC construction company, operating on the West Coast of Canada and USA. Logo attached.
Industry/Entity Type
Construction - Plumbing & HVAC
Contact Information for Business Card
Name, address, phone numbers, email, website address
Look and feel
Each slider illustrates characteristics of the customer's brand and the style your logo design should communicate.

```html
<!DOCTYPE html>
<html lang="en">
<head>
<meta charset="utf-8">
<title>Cedar Ridge Mechanical – Business Card</title>
<link href="https://fonts.googleapis.com/css2?family=Montserrat:wght@400;700&family=Oswald:wght@500&display=swap" rel="stylesheet">
<style>
  :root {
    --backdrop: #c8c8c8;
    --card: #ffffff;
    --ink: #111111;
    --accent-grey: #8a8a8a;
    --muted: #555555;
  }
  * { margin: 0; padding: 0; box-sizing: border-box; }
  html, body { width: 1200px; height: 896px; overflow: hidden; }
  body {
    background: var(--backdrop);
    font-family: "Montserrat", sans-serif;
    color: var(--ink);
    position: relative;
  }
  .card {
    position: absolute;
    left: 334px;
    width: 528px;
    height: 300px;
    background: var(--card);
    border-radius: 24px;
    overflow: hidden;
  }
  .card--front { top: 126px; }
  .card--back { top: 474px; }

  .wordmark {
    display: flex;
    align-items: center;
    gap: 12px;
    font-family: "Oswald", sans-serif;
    font-weight: 500;
    color: var(--ink);
    letter-spacing: 1px;
    text-transform: uppercase;
    white-space: nowrap;
  }
  .wordmark__square {
    background: var(--ink);
    flex: none;
  }
  .card--front .wordmark {
    position: absolute;
    inset: 0;
    justify-content: center;
    font-size: 34px;
  }
  .card--front .wordmark__square { width: 34px; height: 34px; }

  .card__corner-art {
    position: absolute;
    left: 0;
    top: 0;
    width: 220px;
    height: 116px;
    background: linear-gradient(135deg, var(--ink) 0%, var(--ink) 55%, var(--accent-grey) 100%);
  }
  .card--back .wordmark {
    position: absolute;
    right: 18px;
    top: 66px;
    font-size: 20px;
    gap: 9px;
  }
  .card--back .wordmark__square { width: 20px; height: 20px; }

  .person {
    position: absolute;
    left: 23px;
    top: 154px;
  }
  .person__name {
    font-weight: 700;
    font-size: 20px;
    letter-spacing: 0.5px;
  }
  .person__role {
    font-size: 14.5px;
    color: var(--muted);
    margin-top: 2px;
  }
  .contact {
    position: absolute;
    left: 21px;
    top: 221px;
    list-style: none;
    font-size: 14.5px;
  }
  .contact li {
    display: flex;
    align-items: center;
    gap: 6px;
    height: 21px;
  }
  .contact svg { width: 11px; height: 11px; flex: none; }
  .address {
    position: absolute;
    right: 19px;
    top: 241px;
    text-align: right;
    font-size: 14.5px;
    font-style: normal;
    line-height: 21px;
  }
</style>
</head>
<body>

<section class="card card--front" aria-label="Card front">
  <div class="wordmark">
    <span class="wordmark__square"></span>
    <span>Cedar Ridge Mechanical</span>
  </div>
</section>

<section class="card card--back" aria-label="Card back">
  <div class="card__corner-art" role="img" aria-label="Decorative black and grey corner artwork"></div>

  <div class="wordmark">
    <span class="wordmark__square"></span>
    <span>Cedar Ridge Mechanical</span>
  </div>

  <div class="person">
    <p class="person__name">DANIEL REEVES</p>
    <p class="person__role">Managing Director</p>
  </div>

  <ul class="contact">
    <li>
      <svg viewBox="0 0 12 12"><path d="M2.5 0.8 L4.6 3 L3.5 4.4 C4.2 5.9 6 7.7 7.6 8.5 L9 7.4 L11.2 9.5 L9.8 11.2 C5.5 11 1 6.5 0.8 2.2 Z" fill="var(--ink)"/></svg>
      <span>123 456 789</span>
    </li>
    <li>
      <svg viewBox="0 0 12 12"><rect x="0.8" y="2.3" width="10.4" height="7.6" fill="none" stroke="var(--ink)" stroke-width="1.3"/><path d="M1 2.6 L6 6.6 L11 2.6" fill="none" stroke="var(--ink)" stroke-width="1.3"/></svg>
      <span>info@yourgmail.com</span>
    </li>
    <li>
      <svg viewBox="0 0 12 12"><circle cx="6" cy="6" r="5" fill="none" stroke="var(--ink)" stroke-width="1.3"/><path d="M1 6 H11 M6 1 C3.5 3.5 3.5 8.5 6 11 M6 1 C8.5 3.5 8.5 8.5 6 11" fill="none" stroke="var(--ink)" stroke-width="1"/></svg>
      <span>www.yourwebsite.com</span>
    </li>
  </ul>

  <address class="address">
    Your address, City<br>
    State, Zip 1234
  </address>
</section>

</body>
</html>
```